Kelvor Engineers: Why you should hire us keepsake

New design. Open to plastic cards. We are an engineering firm that designs cell phone towers and commercial buildings. Please check out our website www.kelvorstruct.com for more details. We want people to remember our card and for it to be useful if possible. We want the same look and feel on these cards to be translated to other marketing material we may need such as brochures.

Target Market(s)

Architects, Developers and Telecommunication Carriers

Industry/Entity Type

Engineering

Contact Information for Business Card

Card with our company colors, logo, and innovative design with elements related to our industry.

Font styles to use
Sans Serif

Colors
9bcb3c
abd036
0255a3

Requirements
Must have
• Sleek and hip design
Nice to have
• Bright lime green and navy coloring that pops with an innovative design.
Should not have
• A basic and boring design

```html
<!DOCTYPE html>
<html lang="en">
<head>
<meta charset="utf-8">
<title>Kelvor Engineers – Business Card</title>
<link rel="stylesheet" href="https://fonts.googleapis.com/css2?family=Roboto:wght@400;700&family=Roboto+Condensed:wght@700&display=swap">
<style>
  :root {
    --backdrop: #1f1f1f;
    --lime: #00ff00;
    --navy: #022b5c;
    --paper: #f1f1f1;
    --white: #ffffff;
  }
  * { margin: 0; padding: 0; box-sizing: border-box; }
  html, body { width: 1200px; height: 960px; overflow: hidden; }
  body {
    background: var(--backdrop);
    font-family: "Roboto", Arial, sans-serif;
    position: relative;
  }
  .card {
    position: absolute;
    left: 320px;
    width: 600px;
    height: 342px;
    border-radius: 18px;
    overflow: hidden;
  }
  /* Front */
  .card-front { top: 106px; background: var(--lime); }
  .brand-name {
    position: absolute;
    left: 0; right: 0;
    text-align: center;
    font-family: "Roboto", Arial, sans-serif;
    font-weight: 700;
    color: var(--navy);
    line-height: 1;
  }
  .card-front .brand-name { top: 128px; font-size: 96px; letter-spacing: -1px; }
  .tagline {
    position: absolute;
    top: 270px; left: 0; right: 0;
    display: flex; justify-content: center; align-items: center; gap: 6px;
    color: var(--white);
    font-weight: 700;
    font-size: 14px;
  }
  .tagline .rule { width: 28px; height: 1.5px; background: var(--white); }
  .cities {
    position: absolute;
    top: 290px; left: 0; right: 0;
    text-align: center;
    color: var(--white);
    font-size: 14px;
    letter-spacing: 0.4px;
  }
  /* Back */
  .card-back { top: 493px; background: var(--paper); }
  .contact-panel {
    position: absolute;
    left: 0; top: 90px;
    width: 270px; height: 158px;
    background: var(--navy);
    padding: 22px 0 0 35px;
  }
  .person-name {
    font-family: "Roboto Condensed", "Arial Narrow", sans-serif;
    font-weight: 700;
    font-size: 21px;
    color: var(--lime);
    margin-bottom: 10px;
  }
  .contact-list { list-style: none; }
  .contact-list li {
    display: flex; align-items: center; gap: 9px;
    color: var(--white);
    font-size: 14px;
    height: 19px;
  }
  .contact-list svg { width: 14px; height: 14px; fill: var(--lime); flex: none; }
  .card-back .brand-name {
    top: 136px; left: 310px; right: auto; width: 250px;
    font-size: 62px;
  }
  .edge-bar {
    position: absolute;
    right: 0; top: 90px;
    width: 18px; height: 158px;
    background: var(--lime);
  }
</style>
</head>
<body>
  <section class="card card-front" aria-label="Card front">
    <div class="brand-name">Kelvor</div>
    <div class="tagline"><span class="rule"></span>MULTI-DISCIPLINE ENGINEERING<span class="rule"></span></div>
    <div class="cities">Atlanta | Charlotte | Houston | San Antonio</div>
  </section>

  <section class="card card-back" aria-label="Card back">
    <div class="contact-panel">
      <div class="person-name">DANA HOLLOWAY PRATT</div>
      <ul class="contact-list">
        <li><svg viewBox="0 0 24 24"><path d="M6.6 10.8a15.1 15.1 0 0 0 6.6 6.6l2.2-2.2c.3-.3.7-.4 1-.2 1.1.4 2.3.6 3.6.6.6 0 1 .4 1 1V20c0 .6-.4 1-1 1A17 17 0 0 1 3 4c0-.6.4-1 1-1h3.5c.6 0 1 .4 1 1 0 1.3.2 2.5.6 3.6.1.3 0 .7-.2 1z"/></svg>404.555.0132</li>
        <li><svg viewBox="0 0 24 24"><path d="M7 1h10a2 2 0 0 1 2 2v18a2 2 0 0 1-2 2H7a2 2 0 0 1-2-2V3a2 2 0 0 1 2-2zm0 3v14h10V4z"/></svg>706.555.0198</li>
        <li><svg viewBox="0 0 24 24"><path d="M2 5h20v14H2zm2 2v.4l8 5 8-5V7l-8 5z"/></svg>dpratt@kelvorstruct.com</li>
        <li><svg viewBox="0 0 24 24"><path d="M12 2a10 10 0 1 0 0 20 10 10 0 0 0 0-20zm-1 17.9A8 8 0 0 1 4.2 10L9 15v1a2 2 0 0 0 2 2zm6.9-2.5A2 2 0 0 0 16 16h-1v-3a1 1 0 0 0-1-1H8v-2h2a1 1 0 0 0 1-1V7h2a2 2 0 0 0 2-2v-.4a8 8 0 0 1 2.9 12.8z"/></svg>www.kelvorstruct.com</li>
      </ul>
    </div>
    <div class="brand-name">Kelvor</div>
    <div class="edge-bar"></div>
  </section>
</body>
</html>
```